I need a SEO-friendly Wordpress website (making sure to style H1, H2, H3, etc correctly) for a Hawaii-based law firm called Meridian Crest Legal Group. Comparable websites include https://brvlaw.example/ and https://www.lomrit.example/ for design reference. The current copy on the TarnAdvocate.example website can be used.

```html
<!DOCTYPE html>
<html lang="en">
<head>
<meta charset="utf-8">
<title>Meridian Crest Legal Group – Meridian Lawyers</title>
<link rel="stylesheet" href="https://fonts.googleapis.com/css2?family=Roboto:wght@400;500;700&family=Roboto+Slab:wght@400;700&display=swap">
<style>
:root{
  --accent:#9a3d1f;
  --accent-box:rgba(140,52,20,.88);
  --ink:#1c2533;
  --muted:#6b6f76;
  --line:#dcdcdc;
  --peach:#f5ebe3;
  --footer:#121316;
  --white:#fff;
}
*{box-sizing:border-box;margin:0;padding:0}
html,body{width:1200px;height:2952px;overflow:hidden}
body{font-family:"Roboto",Arial,sans-serif;color:var(--ink);background:var(--white)}
h1,h2,h3{font-family:"Roboto Slab",Georgia,serif}
a{color:inherit;text-decoration:none}

/* header */
.site-header{height:130px;padding:0 60px;display:flex;justify-content:space-between;align-items:center}
.brand-name{font-size:29px;font-weight:700;color:var(--ink)}
.brand-tag{font-size:15px;font-weight:700;color:var(--accent);margin-top:6px}
.header-right{display:flex;flex-direction:column;align-items:flex-end;gap:22px}
.contact-row{display:flex;align-items:center;gap:26px}
.phone{display:flex;align-items:center;gap:10px;font-size:24px;font-weight:700;color:var(--accent)}
.btn-outline{border:2px solid var(--accent);color:var(--accent);font-size:14px;font-weight:700;padding:9px 18px;letter-spacing:.5px}
.main-nav{display:flex;gap:28px;font-size:15px;font-weight:700}
.main-nav a.active{color:var(--accent)}

/* hero */
.hero{position:relative;height:572px;background:linear-gradient(120deg,#5a5550 0%,#9a948e 35%,#6b655f 65%,#2d2a28 100%)}
.hero-box{position:absolute;left:480px;top:80px;width:632px;height:388px;background:var(--accent-box);padding:48px 52px;color:var(--white)}
.hero-kicker{font-size:16px;letter-spacing:1px}
.hero-box h1{font-family:"Roboto",Arial,sans-serif;font-size:52px;font-weight:700;letter-spacing:1px;margin:14px 0 16px}
.hero-lead{font-size:22px;font-weight:700;line-height:1.5;text-transform:uppercase}
.btn-light{display:inline-block;margin-top:26px;border:2px solid var(--white);padding:14px 26px;font-size:17px;font-weight:500}

/* section heading */
.section-title{text-align:center;font-size:40px;font-weight:700}
.section-title::after{content:"";display:block;width:56px;height:3px;background:var(--accent);margin:14px auto 0}
.section-sub{text-align:center;font-size:14px;color:var(--muted);line-height:1.6;margin:16px auto 0;width:620px}

/* about */
.about{height:688px;padding-top:96px}
.about-cards{display:flex;gap:24px;width:932px;margin:64px auto 0}
.about-card{flex:1;border:1px solid var(--line);box-shadow:0 4px 18px rgba(0,0,0,.08);padding:30px 28px;height:350px}
.about-card h3{font-family:"Roboto",Arial,sans-serif;font-size:22px;font-weight:700;color:var(--accent);line-height:1.4}
.about-card h3::after{content:"";display:block;width:100%;height:1px;background:var(--line);margin-top:14px}
.about-card p{font-size:13px;color:var(--muted);line-height:1.8;margin-top:14px}
.btn-small{display:inline-block;margin-top:22px;border:2px solid var(--accent);color:var(--accent);font-size:12px;font-weight:700;padding:8px 14px}

/* practice areas */
.practice{height:590px;background:linear-gradient(135deg,#f8f1ec 0%,var(--peach) 50%,#f7efe9 100%);padding-top:72px;position:relative}
.practice .section-title{font-size:44px}
.practice .section-title::after{display:none}
.practice .section-sub{margin-top:10px}
.practice-list{display:flex;gap:24px;width:1052px;margin:38px auto 0}
.practice-item{flex:1}
.practice-photo{height:218px;background:linear-gradient(135deg,#3b2d27,#8f7a6c 60%,#cfc6bd)}
.practice-item h3{font-size:21px;font-weight:700;margin-top:18px}
.practice-item p{font-size:13px;color:var(--muted);line-height:1.7;margin-top:8px;width:260px}
.slider-arrow{position:absolute;top:292px}
.slider-arrow.prev{left:36px}.slider-arrow.next{right:36px}

/* location */
.location{height:688px;padding-top:82px}
.location .section-title::after{display:none}
.location .section-sub{margin-top:8px}
.location-body{display:flex;justify-content:space-between;width:1060px;margin:60px auto 0}
.contact-form{width:400px;display:flex;flex-direction:column;gap:14px;padding-top:10px}
.field{border:1px solid var(--line);height:46px;padding:0 12px;font-size:12px;color:var(--muted);display:flex;align-items:center}
.field.message{height:90px;align-items:flex-start;padding-top:10px}
.btn-send{align-self:flex-start;border:2px solid var(--accent);color:var(--accent);font-size:14px;font-weight:700;padding:12px 18px;margin-top:10px}
.map{position:relative;width:550px;height:350px;background:linear-gradient(160deg,#eef0ea,#e4e8e2)}
.map-card{position:absolute;left:26px;top:22px;width:250px;background:var(--white);box-shadow:0 2px 10px rgba(0,0,0,.18);padding:14px 16px;font-size:12.5px;line-height:1.7}
.map-card b{color:var(--ink)}
.map-pin{position:absolute;left:380px;top:200px}

/* footer */
.site-footer{height:284px;background:linear-gradient(135deg,#1a1b1f,var(--footer) 60%,#202227);color:var(--white);text-align:center;padding-top:40px}
.social{display:flex;justify-content:center;gap:14px}
.social span{width:42px;height:42px;border:2px solid var(--white);border-radius:50%}
.footer-nav{display:flex;justify-content:center;gap:26px;font-size:12px;font-weight:700;margin-top:32px}
.footer-rule{width:700px;height:1px;background:#3a3c42;margin:30px auto 0}
.copyright{font-size:12px;margin-top:22px;color:#d7d7d7}
</style>
</head>
<body>

<header class="site-header">
  <div class="brand">
    <div class="brand-name">Meridian Crest Legal Group</div>
    <div class="brand-tag">Divorce and Personal Injury Lawyers</div>
  </div>
  <div class="header-right">
    <div class="contact-row">
      <a class="phone" href="tel:18085550142">
        <svg width="22" height="22" viewBox="0 0 24 24"><path fill="#9a3d1f" d="M6.6 10.8a15.1 15.1 0 0 0 6.6 6.6l2.2-2.2c.3-.3.7-.4 1-.2 1.1.4 2.3.6 3.6.6.6 0 1 .4 1 1V20c0 .6-.4 1-1 1A17 17 0 0 1 3 4c0-.6.4-1 1-1h3.5c.6 0 1 .4 1 1 0 1.3.2 2.5.6 3.6.1.3 0 .7-.2 1z"/></svg>
        +1.808.555.0142
      </a>
      <a class="btn-outline" href="#">FREE CONSULTATION</a>
    </div>
    <nav class="main-nav">
      <a class="active" href="#">HOME</a><a href="#">ABOUT US</a><a href="#">PRACTICE AREA</a><a href="#">ATTORNEYS</a><a href="#">BLOG</a><a href="#">CONTACT</a>
    </nav>
  </div>
</header>

<section class="hero" role="img" aria-label="Photo of a lawyer's desk with documents, glasses and a laptop">
  <div class="hero-box">
    <div class="hero-kicker">OVER 15 YEARS OF PRACTICE</div>
    <h1>MERIDIAN LAWYERS</h1>
    <p class="hero-lead">Dedicated to making sure you receive the care and attention you need.</p>
    <a class="btn-light" href="#">READ MORE</a>
  </div>
</section>

<section class="about">
  <h2 class="section-title">About the Meridian Lawyers of MCLG</h2>
  <p class="section-sub">Our team serves families and individuals across the islands with steady counsel, clear advice and careful preparation in every matter we take on.</p>
  <div class="about-cards">
    <article class="about-card">
      <h3>Lawyers Serving the Big Island &amp; Neighboring Islands</h3>
      <p>The experienced attorneys of Meridian Crest Legal Group's Kailua Kona office provide clients with a wide range of litigation expertise, including legal matters involving divorce &amp; family, personal injury, auto accidents, intellectual property, and real estate. We also offer commercial and hospitality litigation expertise.</p>
      <a class="btn-small" href="#">LEARN MORE</a>
    </article>
    <article class="about-card">
      <h3>Nationwide Law Firm Presence</h3>
      <p>Kailua Kona serves as the West Coast headquarters for litigation and representation on behalf of individuals and corporations involved in a wide range of legal matters. The firm and its attorneys are licensed to practice and represent clients in Hawaii, California, Arizona, Texas, and Washington D.C.</p>
      <a class="btn-small" href="#">LEARN MORE</a>
    </article>
  </div>
</section>

<section class="practice">
  <h2 class="section-title">Areas of Practice</h2>
  <p class="section-sub">Focused guidance for the legal matters our clients face most often.</p>
  <svg class="slider-arrow prev" width="14" height="22" viewBox="0 0 14 22"><path d="M11 2 3 11l8 9" fill="none" stroke="#1c2533" stroke-width="3"/></svg>
  <svg class="slider-arrow next" width="14" height="22" viewBox="0 0 14 22"><path d="m3 2 8 9-8 9" fill="none" stroke="#1c2533" stroke-width="3"/></svg>
  <div class="practice-list">
    <article class="practice-item">
      <div class="practice-photo" role="img" aria-label="Photo of a couple meeting with a family lawyer"></div>
      <h3>Family &amp; Divorce</h3>
      <p>Calm, practical support through separation, custody and support matters.</p>
    </article>
    <article class="practice-item">
      <div class="practice-photo" role="img" aria-label="Photo of an injury consultation at an office table"></div>
      <h3>Personal Injury</h3>
      <p>Representation for accident victims seeking fair and full compensation.</p>
    </article>
    <article class="practice-item">
      <div class="practice-photo" role="img" aria-label="Photo of a property contract being signed"></div>
      <h3>Real Estate</h3>
      <p>Advice on purchases, leases, disputes and title questions across Hawaii.</p>
    </article>
  </div>
</section>

<section class="location">
  <h2 class="section-title">Location</h2>
  <p class="section-sub">Visit our Kailua Kona office or send us a message and we will respond promptly.</p>
  <div class="location-body">
    <form class="contact-form">
      <div class="field">Enter Name</div>
      <div class="field">Enter Email</div>
      <div class="field">Subject</div>
      <div class="field message">Message</div>
      <div class="btn-send">SEND MESSAGE</div>
    </form>
    <div class="map" role="img" aria-label="Street map of Kailua Kona showing the office location">
      <div class="map-card">
        <b>Address :</b><br>
        48-210 Harborview Lane, Suite 12<br>
        Kailua Kona, Hawaii 96740<br>
        <b>Phone :</b> +1.808.555.0142<br>
        <b>Email :</b> clients@tarnadvocate.example
      </div>
      <svg class="map-pin" width="26" height="36" viewBox="0 0 26 36"><path d="M13 0C5.8 0 0 5.8 0 13c0 9.7 13 23 13 23s13-13.3 13-23C26 5.8 20.2 0 13 0z" fill="#d93a2b"/><circle cx="13" cy="13" r="4.5" fill="#8c1d14"/></svg>
    </div>
  </div>
</section>

<footer class="site-footer">
  <div class="social" aria-label="Social links"><span></span><span></span><span></span><span></span><span></span></div>
  <nav class="footer-nav">
    <a href="#">HOME</a><a href="#">ABOUT US</a><a href="#">PRACTICE AREA</a><a href="#">ATTORNEYS</a><a href="#">BLOG</a><a href="#">CONTACT US</a>
  </nav>
  <div class="footer-rule"></div>
  <p class="copyright">Copyrights © 2015 Meridian Crest Legal Group. All Rights Reserved. Terms of Use | Privacy Policy</p>
</footer>

</body>
</html>
```